Web Design for an Innovative Life Science Marketplace

IMPORTANT:
The software is called CS-Cart. It has capabilities and limitations with design features in the software. There is a certain framework that needs to be followed. It is PHP and Linux. It may require add-ons for your design, so please be specific with what is required. It’s preferred the designer has CS-Cart knowledge/experience.

Key Requirements
1. I’d like the design to include an implemented/recommended CS-Cart theme that is consistent with our branding (see the marketing collateral and logo).
2. I then need the additional design changes to that theme to create the below web pages.
3. All designs should be consistent with our branding. All pictures should either be computer generated (clip art-like) or pictures of happy patients. What is a happy patient? Close up photo of someone healthy, happy, and experiencing/enjoying life. Not someone in a hospital or getting care. Please see examples already on the site.

Please see the attached Web Design details in the word document. That document is important to complete the design.

```html
<!DOCTYPE html>
<html lang="en">
<head>
<meta charset="utf-8">
<title>LabLoop — Circular Supply Chain Marketplace</title>
<link href="https://fonts.googleapis.com/css2?family=Montserrat:wght@400;600;700;800&family=Open+Sans:wght@400;600&display=swap" rel="stylesheet">
<style>
:root{
  --green:#7cc242;
  --green-dark:#5fa82c;
  --teal:#1f8f7f;
  --teal-dark:#16705f;
  --teal-mid:#2aa08d;
  --ink:#2b2b2b;
  --muted:#777;
  --grey-bg:#f2f2f2;
  --white:#fff;
  --black:#111;
}
*{box-sizing:border-box;margin:0;padding:0}
html,body{width:1200px;height:2808px;overflow:hidden}
body{font-family:"Open Sans",Arial,sans-serif;color:var(--ink);background:var(--white);position:relative}
h1,h2,h3,.btn,.nav a,.brand{font-family:"Montserrat",Arial,sans-serif}

/* header */
.site-header{height:100px;display:flex;align-items:center;justify-content:space-between;padding:0 40px 0 70px}
.brand{display:flex;align-items:center;gap:12px;font-weight:800;font-size:30px;color:var(--teal-dark);letter-spacing:1px}
.brand-dot{width:34px;height:34px;border-radius:50%;background:var(--green)}
.header-tools{display:flex;align-items:center;gap:30px}
.search{width:250px;height:38px;border:1px solid #ccc;border-radius:3px;display:flex;align-items:center;justify-content:space-between;padding:0 12px;font-size:14px;color:#999}
.cart{display:flex;align-items:center;gap:10px;font-size:12px;color:var(--muted)}
.cart strong{display:block;font-size:18px;color:var(--ink)}

/* nav */
.nav{height:48px;background:var(--green);display:flex;padding-left:70px}
.nav a{display:flex;align-items:center;padding:0 24px;color:var(--white);font-size:14px;font-weight:600;text-decoration:none;letter-spacing:.5px}
.nav a.active{background:var(--green-dark)}

/* hero */
.hero{position:relative;height:512px;background:linear-gradient(100deg,#e9dcb5 0%,#c9d88a 40%,#9fcf5a 70%,#7fbf3a 100%)}
.hero-photo{position:absolute;left:0;top:0;width:640px;height:512px;background:radial-gradient(ellipse at 45% 45%,#f1d7bf 0%,#dbc08e 45%,rgba(180,200,110,0) 75%)}
.hero-copy{position:absolute;left:700px;top:100px;width:440px;color:var(--white)}
.hero-copy h1{font-size:42px;font-weight:800;line-height:1.12;text-transform:uppercase;margin-bottom:22px}
.hero-copy p{font-size:17px;line-height:1.55;margin-bottom:26px}
.btn{display:inline-block;background:var(--black);color:var(--white);font-weight:700;font-size:15px;padding:13px 22px;text-transform:uppercase;letter-spacing:.5px;border-radius:2px}

/* roles */
.roles{display:flex;height:280px}
.role{flex:1;color:var(--white);text-align:center;padding-top:30px}
.role.manufacturers{background:var(--teal);clip-path:polygon(0 0,100% 0,100% 78%,0 100%)}
.role.researchers{background:var(--white);color:var(--teal-dark);clip-path:polygon(0 0,100% 0,100% 78%,50% 100%,0 78%)}
.role.suppliers{background:var(--teal);clip-path:polygon(0 0,100% 0,100% 100%,0 78%)}
.role svg{width:76px;height:76px;margin-bottom:14px}
.role h3{font-size:22px;font-weight:800;text-transform:uppercase;font-style:normal;margin-bottom:10px}
.role p{font-size:14px;line-height:1.45;width:300px;margin:0 auto;opacity:.9}

/* promise */
.promise{position:relative;height:300px}
.promise-couple{position:absolute;left:0;top:20px;width:300px;height:260px;background:radial-gradient(ellipse at 50% 50%,#d8d1cb 0%,#eeeae6 60%,#fff 85%)}
.promise-child{position:absolute;right:40px;top:20px;width:260px;height:270px;background:radial-gradient(ellipse at 50% 50%,#f3dcc4 0%,#cfe6f3 55%,#fff 85%)}
.promise-copy{position:absolute;left:320px;width:560px;top:90px;text-align:center}
.section-title{font-size:46px;font-weight:700;color:var(--green)}
.section-title.dark{color:var(--teal-dark)}
.promise-copy p{margin-top:18px;font-size:15px;color:var(--muted);line-height:1.55}

/* products */
.products{height:520px;background:var(--grey-bg);padding-top:70px;text-align:center}
.product-row{display:flex;justify-content:center;gap:18px;margin-top:46px}
.product{width:250px;height:250px;background:var(--white);padding:30px 20px;box-shadow:0 2px 8px rgba(0,0,0,.06)}
.product.featured{transform:translateY(-14px);box-shadow:0 8px 22px rgba(0,0,0,.15)}
.product .icon{width:80px;height:80px;border-radius:50%;border:3px solid var(--green);margin:0 auto 18px;display:flex;align-items:center;justify-content:center}
.product h3{font-size:17px;font-weight:700;color:var(--teal-dark);margin-bottom:10px}
.product p{font-size:13px;color:var(--muted);line-height:1.5}

/* about */
.about{height:380px;text-align:center;padding:60px 150px 0}
.about p{font-size:15px;color:var(--muted);line-height:1.6;margin-top:22px}
.about .btn{margin-top:28px}

/* resources */
.resources{display:flex;height:400px}
.resource{flex:1;color:var(--white);text-align:center;padding-top:130px}
.resource.paper{background:var(--teal);clip-path:polygon(0 15%,100% 0,100% 100%,0 100%)}
.resource.brochure{background:var(--green);clip-path:polygon(0 0,100% 15%,100% 100%,0 100%)}
.resource h2{font-size:30px;font-weight:800;text-transform:uppercase}
.resource p{width:420px;margin:18px auto 26px;font-size:14px;line-height:1.55}
.btn.light{background:var(--white);color:var(--teal-dark);border:2px solid var(--white)}

/* footer */
.site-footer{height:220px;display:flex;gap:70px;padding:40px 70px 0}
.site-footer h4{font-family:"Montserrat",Arial,sans-serif;font-size:16px;font-weight:700;margin-bottom:18px}
.links{display:grid;grid-template-columns:110px 140px;row-gap:10px;font-size:13px;color:var(--muted)}
.contact li{list-style:none;display:flex;gap:10px;align-items:center;font-size:13px;color:var(--muted);margin-bottom:10px}
.contact svg{width:16px;height:16px;flex:none}
.newsletter{margin-left:auto;width:330px}
.newsletter p{font-size:13px;color:var(--muted);margin-bottom:14px}
.subscribe{display:flex}
.subscribe span{flex:1;height:40px;border:1px solid #ccc;font-size:13px;color:#999;padding:10px}
.subscribe b{width:44px;height:40px;background:var(--teal)}
.bottom-bar{position:absolute;left:0;bottom:0;width:1200px;height:48px;background:var(--teal-dark);color:var(--white);display:flex;align-items:center;justify-content:center;font-size:13px;gap:8px}
</style>
</head>
<body>

<header class="site-header">
  <div class="brand"><span class="brand-dot"></span>LABLOOP</div>
  <div class="header-tools">
    <div class="search">Type here... <svg width="16" height="16" viewBox="0 0 16 16"><circle cx="6.5" cy="6.5" r="5" fill="none" stroke="#888" stroke-width="2"/><line x1="10" y1="10" x2="15" y2="15" stroke="#888" stroke-width="2"/></svg></div>
    <div class="cart"><svg width="34" height="30" viewBox="0 0 34 30"><path d="M2 3h6l4 16h16l4-12H10" fill="none" stroke="#1f8f7f" stroke-width="3"/><circle cx="14" cy="25" r="3" fill="#1f8f7f"/><circle cx="26" cy="25" r="3" fill="#1f8f7f"/></svg><div>MY CART<strong>$210</strong></div></div>
  </div>
</header>

<nav class="nav">
  <a class="active">HOME</a><a>ABOUT US</a><a>WHY LABLOOP</a><a>PARTNER</a><a>WHITE PAPER</a><a>QUALITY POLICY</a><a>CONTACT US</a>
</nav>

<section class="hero">
  <div class="hero-photo" role="img" aria-label="Photo of a smiling woman outdoors in warm sunlight"></div>
  <div class="hero-copy">
    <h1>Join the Circular Supply Chain</h1>
    <p>A virtual multi-vendor marketplace and for the life sciences community to connect and transact before and after-market materials and equipment</p>
    <span class="btn">Pre-Register Today</span>
  </div>
</section>

<section class="roles">
  <div class="role manufacturers">
    <svg viewBox="0 0 76 76"><circle cx="38" cy="38" r="34" fill="none" stroke="#fff" stroke-width="3"/><path d="M20 52V34l10 6v-6l10 6v-6l10 6V24h6v28z" fill="#fff"/></svg>
    <h3>Manufacturers</h3>
    <p>Create an income in minutes by listing unused materials and equipment</p>
  </div>
  <div class="role researchers">
    <svg viewBox="0 0 76 76"><circle cx="38" cy="38" r="34" fill="none" stroke="#16705f" stroke-width="3"/><circle cx="38" cy="30" r="8" fill="#16705f"/><path d="M24 54c2-10 8-14 14-14s12 4 14 14z" fill="#16705f"/></svg>
    <h3>Researchers</h3>
    <p>Find the materials and equipment you need at reduced prices</p>
  </div>
  <div class="role suppliers">
    <svg viewBox="0 0 76 76"><circle cx="38" cy="38" r="34" fill="none" stroke="#fff" stroke-width="3"/><rect x="22" y="28" width="32" height="24" fill="none" stroke="#fff" stroke-width="3"/><path d="M22 28l16-8 16 8" fill="none" stroke="#fff" stroke-width="3"/></svg>
    <h3>Original Suppliers</h3>
    <p>Market your products across a broad life sciences network</p>
  </div>
</section>

<section class="promise">
  <div class="promise-couple" role="img" aria-label="Photo of a smiling older couple"></div>
  <div class="promise-copy">
    <h2 class="section-title">Our Promise</h2>
    <p>To provide a more efficient and quality driven supply chain through a collaborative life sciences marketplace</p>
  </div>
  <div class="promise-child" role="img" aria-label="Photo of a happy young child with arms raised"></div>
</section>

<section class="products">
  <h2 class="section-title">Our Products</h2>
  <div class="product-row">
    <div class="product"><div class="icon"><svg width="40" height="40" viewBox="0 0 40 40"><path d="M15 4h10M17 4v12L6 34h28L23 16V4" fill="none" stroke="#16705f" stroke-width="3"/></svg></div><h3>Raw Materials</h3><p>Consumables and starting materials for drift and intermediates manufacturing or research</p></div>
    <div class="product featured"><div class="icon"><svg width="40" height="40" viewBox="0 0 40 40"><rect x="6" y="10" width="28" height="20" fill="none" stroke="#16705f" stroke-width="3"/><line x1="12" y1="34" x2="28" y2="34" stroke="#16705f" stroke-width="3"/></svg></div><h3>Equipment</h3><p>We believe in a second life for lab equipment with our partners</p></div>
    <div class="product"><div class="icon"><svg width="40" height="40" viewBox="0 0 40 40"><circle cx="20" cy="20" r="7" fill="none" stroke="#16705f" stroke-width="3"/><path d="M20 4v6M20 30v6M4 20h6M30 20h6" stroke="#16705f" stroke-width="3"/></svg></div><h3>Parts</h3><p>We help you find spare parts, services and trusted maintenance specialists</p></div>
    <div class="product"><div class="icon"><svg width="40" height="40" viewBox="0 0 40 40"><circle cx="20" cy="20" r="8" fill="none" stroke="#16705f" stroke-width="3"/><path d="M20 6v6M20 28v6M6 20h6M28 20h6M10 10l4 4M26 26l4 4M30 10l-4 4M14 26l-4 4" stroke="#16705f" stroke-width="3"/></svg></div><h3>Collaborative Relationships</h3><p>Our first step is to build our network of trusted partners</p></div>
  </div>
</section>

<section class="about">
  <h2 class="section-title dark">About Us</h2>
  <p>We are the first ever private and virtual B2B marketplace and community for the life science manufacturers, researchers, and vendors to sell, purchase and transact pristine and aftermarket materials and equipment as well as collaborate on new scientific networks.</p>
  <p>We are in the developmental phase of our platform working with some of the most trusted and best partners. We are tentatively scheduled for an exclusive launch before the end of the year.</p>
  <span class="btn">Learn More</span>
</section>

<section class="resources">
  <div class="resource paper">
    <h2>Our White Paper</h2>
    <p>A virtual multi-vendor marketplace and for the life sciences community to connect and transact before and after-market materials and equipment.</p>
    <span class="btn light">Read Our White Paper</span>
  </div>
  <div class="resource brochure">
    <h2>Our Brochure</h2>
    <p>A virtual multi-vendor marketplace and for the life sciences community to connect and transact before and after-market materials and equipment.</p>
    <span class="btn light">Read Our Brochure</span>
  </div>
</section>

<footer class="site-footer">
  <div>
    <h4>USEFUL LINKS</h4>
    <div class="links"><span>Home</span><span>Sign In</span><span>About</span><span>How It Works</span><span>Products</span><span>Quality Policy</span><span>White Paper</span><span>Privacy Policy</span></div>
  </div>
  <div class="contact">
    <h4>CONTACT US</h4>
    <ul>
      <li><svg viewBox="0 0 16 16"><path d="M8 1a5 5 0 0 0-5 5c0 4 5 9 5 9s5-5 5-9a5 5 0 0 0-5-5z" fill="#1f8f7f"/></svg>214 Orchard Lane, Fairview, OH 44120</li>
      <li><svg viewBox="0 0 16 16"><path d="M3 1h3l1 4-2 1a9 9 0 0 0 5 5l1-2 4 1v3a2 2 0 0 1-2 2A13 13 0 0 1 1 3a2 2 0 0 1 2-2z" fill="#1f8f7f"/></svg>+1 555 014 2280</li>
      <li><svg viewBox="0 0 16 16"><rect x="1" y="3" width="14" height="10" fill="#1f8f7f"/><path d="M1 3l7 6 7-6" fill="none" stroke="#fff"/></svg>hello@labloop.example</li>
    </ul>
  </div>
  <div class="newsletter">
    <h4>Newsletter</h4>
    <p>Sign up to get updates from LABLOOP</p>
    <div class="subscribe"><span>Type here...</span><b></b></div>
  </div>
</footer>

<div class="bottom-bar"><span>LABLOOP · 2018 · Powered by MarketForge Suite</span></div>

</body>
</html>
```